WEBSITE DESIGN, VELTRA paint and panel

We are in need of a website for Veltra Paint & Panel based in Brisbane, Australia. We are a boutique Automotive Paint & Panel Company that provides services to all makes and models of vehicles. We have attached a logo that is still in draft stage but gives you an idea of the colour scheme and fonts and overall impact we are looking for. We are after a white background so this is clean and crisp whilst being sleek, modern and professional. The website must represent our slogan of Glowing finish on the Gleaming frame. The website must therefore be visually effective as our product is to get colour and placement on vehicle body's correct so the website must have this impact on our clients. We are after a widescreen webpage that is simple and logical to navigate. The final design should give clients the confidence that we can deliver on our promise.
Updates

Target Market(s)

Vehicle Owners who have a need for panel repairs and people who want to reinvigorate their car with a new coat of paint.

Industry/Entity Type

Car Repair

Coding

Coded - Design and coding required

Number of Pages Required

5+ page

Font styles to use
Sans Serif

Colors
ffffff
ffc214
000000

Requirements
Must have
• Page 1 - Home Page
• Page 2 - Our Process
• Page 3 - Private Customers
• Page 4 - Fleet & Corporate
• Page 5 - Insurance
• Page 6 - Get a Quote
• Page 7 - Connect (Contacts Page)
• Same font and colour scheme as the logo.
Should not have
• A typical mechanical/paint and panel layout which looks like a template website.

```html
<!DOCTYPE html>
<html lang="en">
<head>
<meta charset="utf-8">
<title>Veltra Paint &amp; Panel</title>
<link rel="stylesheet" href="https://fonts.googleapis.com/css2?family=Open+Sans:wght@400;600;700&display=swap">
<style>
:root{
  --orange:#f7a21b;
  --ink:#222222;
  --text:#6a6a6a;
  --header:#1e1e1e;
  --dark:#151a1f;
  --white:#ffffff;
  --line:#d9d9d9;
  --footer:#1b1b1b;
}
*{box-sizing:border-box;margin:0;padding:0}
html,body{width:1200px;height:2192px;overflow:hidden;background:var(--white)}
body{font-family:"Open Sans",Arial,sans-serif;color:var(--text);position:relative}
.site-header{position:absolute;top:0;left:0;width:1200px;height:128px;background:var(--header)}
.brand{position:absolute;left:56px;top:34px;display:flex;align-items:center;gap:10px;color:var(--white);font-size:26px;font-weight:600;letter-spacing:3px}
.brand-dot{width:14px;height:14px;background:var(--orange);border-radius:50%}
.main-nav{position:absolute;left:56px;top:84px;display:flex;height:44px}
.main-nav a{display:block;padding:0 26px;line-height:44px;color:var(--white);font-size:15px;text-decoration:none}
.main-nav a.active{background:var(--orange)}
.call{position:absolute;right:56px;top:36px;display:flex;align-items:center;gap:10px;color:var(--white);font-size:15px}
.call strong{color:var(--orange);font-weight:600}
.hero{position:absolute;top:128px;left:0;width:1200px;height:640px;background:linear-gradient(120deg,#2a5fa8 0%,#1c8de0 30%,#3b4a5c 60%,#6c7480 100%)}
.hero-caption{position:absolute;left:56px;top:330px;background:rgba(20,20,20,.55);padding:22px 40px 22px 20px;color:var(--white);font-size:38px;font-weight:600;letter-spacing:2px;line-height:1.3;text-transform:uppercase}
.hero-next{position:absolute;right:60px;top:250px}
.section-title{text-align:center;font-size:40px;font-weight:700;color:var(--ink);letter-spacing:2px;text-transform:uppercase;line-height:54px}
.section-title span{color:var(--orange)}
.intro{width:860px;margin:0 auto;text-align:center;font-size:15px;line-height:26px}
.services{position:absolute;top:792px;left:0;width:1200px;height:370px}
.services .intro{margin-top:18px}
.tiles{position:absolute;top:150px;left:0;width:1200px;height:220px;display:flex}
.tile{position:relative;width:300px;height:220px}
.tile-label{position:absolute;left:0;right:0;bottom:22px;text-align:center;color:var(--white);font-size:16px;font-weight:600;text-transform:uppercase;letter-spacing:1px}
.tile.feature .tile-overlay{position:absolute;inset:0;background:rgba(247,162,27,.78)}
.tile.feature .tile-label{top:40px;bottom:auto}
.tile-more{position:absolute;left:100px;top:134px;width:100px;border-top:1px solid var(--white);border-bottom:1px solid var(--white);line-height:30px;text-align:center;color:var(--white);font-size:13px;font-weight:600}
.about{position:absolute;top:1204px;left:0;width:1200px}
.about .intro{margin-top:18px}
.btn{display:block;margin:20px auto 0;width:160px;height:40px;background:var(--orange);color:var(--white);font-size:14px;font-weight:600;text-align:center;line-height:40px;text-transform:uppercase}
.testimonials{position:absolute;top:1448px;left:0;width:1200px;height:272px;background:linear-gradient(90deg,#10161c,#273340 50%,#10161c)}
.testimonials .section-title{color:var(--white);font-size:34px;padding-top:18px}
.quotes{display:flex;justify-content:center;gap:60px;margin-top:24px}
.quote{display:flex;gap:20px;width:470px}
.avatar{flex:none;width:84px;height:84px;border-radius:50%;background:#9aa3ab;border:3px solid var(--white)}
.quote p{color:#d5d9dd;font-size:15px;line-height:24px}
.quote .more{color:var(--orange);font-size:13px;font-weight:600;margin-top:4px}
.dots{position:absolute;left:0;right:0;bottom:24px;display:flex;justify-content:center;gap:8px}
.dots i{width:10px;height:10px;border-radius:50%;background:#777}
.dots i.on{background:var(--white)}
.quote-form{position:absolute;top:1752px;left:0;width:1200px;height:360px}
.quote-form .section-title{font-size:34px;padding-top:24px}
.fields{position:absolute;top:104px;left:216px;width:768px}
.row{display:flex;gap:24px}
.field{flex:1;height:44px;border:1px solid var(--line);padding:0 18px;line-height:42px;font-size:13px;color:#8a8a8a}
.field.msg{margin-top:24px;height:84px;line-height:20px;padding-top:12px}
.submit{position:absolute;top:282px;left:524px;width:152px;height:48px;background:var(--orange);color:var(--white);font-size:14px;font-weight:600;text-align:center;line-height:48px;text-transform:uppercase}
.site-footer{position:absolute;top:2112px;left:0;width:1200px;height:80px;background:var(--footer)}
.copy{position:absolute;left:56px;top:30px;color:#9a9a9a;font-size:13px}
.social{position:absolute;right:56px;top:22px;display:flex;gap:10px}
.social i{width:34px;height:34px;border-radius:50%;background:var(--white)}
</style>
</head>
<body>
<header class="site-header">
  <div class="brand"><span class="brand-dot"></span>VELTRA</div>
  <div class="call">
    <svg width="18" height="18" viewBox="0 0 24 24"><rect x="1" y="1" width="22" height="22" rx="4" fill="#fff"/><path d="M8 5l2 4-2 1.5c1 2.2 2.8 4 5 5L14.5 14l4 2-1 3c-6.5 0-12.5-6-12.5-12.5z" fill="#1e1e1e"/></svg>
    <span>Call Us <strong>1800 555 010</strong></span>
  </div>
  <nav class="main-nav">
    <a class="active">Home</a><a>Our Process</a><a>Private Customers</a><a>Fleet &amp; Corporate Insurance</a><a>Get a Quote</a><a>Connect</a>
  </nav>
</header>

<section class="hero" role="img" aria-label="Painter in protective mask spraying a blue car panel in a paint booth">
  <div class="hero-caption">Glowing finish on<br>the Gleaming frame</div>
  <svg class="hero-next" width="40" height="40" viewBox="0 0 40 40"><circle cx="20" cy="20" r="18" fill="none" stroke="#fff" stroke-width="2"/><path d="M17 12l8 8-8 8" fill="none" stroke="#fff" stroke-width="2.5"/></svg>
</section>

<section class="services">
  <h2 class="section-title">Our <span>Services</span></h2>
  <p class="intro">We repair and refinish every make and model with care, matching factory colour and restoring panels to their best. Each job is prepared, painted and checked by hand in our Brisbane workshop.</p>
  <div class="tiles">
    <div class="tile" role="img" aria-label="Red car body panel" style="background:linear-gradient(135deg,#b3121b,#e0232e)"><div class="tile-label">Panel &amp; Paint</div></div>
    <div class="tile" role="img" aria-label="Restored white classic car" style="background:linear-gradient(135deg,#8c8f93,#d7d8da)"><div class="tile-label">Auto Restoration</div></div>
    <div class="tile feature" role="img" aria-label="Custom painted car" style="background:linear-gradient(135deg,#6b5a48,#a78a62)"><div class="tile-overlay"></div><div class="tile-label">Custom Paint</div><div class="tile-more">READ MORE</div></div>
    <div class="tile" role="img" aria-label="Technician working on a car wheel" style="background:linear-gradient(135deg,#2b2f36,#5d6570)"><div class="tile-label">Plastic Dip</div></div>
  </div>
</section>

<section class="about">
  <h2 class="section-title">About <span>Us</span></h2>
  <p class="intro">Veltra Paint &amp; Panel is a boutique workshop built on patience and precision. From minor dents to full resprays, our team blends colour by eye and by spectrometer so every panel sits true. We treat each car as if it were our own and stand behind every finish we deliver.</p>
  <div class="btn">Read More</div>
</section>

<section class="testimonials">
  <h2 class="section-title">What Our Customer Say's</h2>
  <div class="quotes">
    <div class="quote"><div class="avatar" role="img" aria-label="Customer portrait"></div><div><p>The bumper came back looking better than new and the colour match is perfect. Quick, friendly and honest from start to finish.</p><div class="more">READ MORE</div></div></div>
    <div class="quote"><div class="avatar" role="img" aria-label="Customer portrait"></div><div><p>Our fleet vans were repaired on time and on budget. The finish is flawless and the team kept us updated every day.</p><div class="more">READ MORE</div></div></div>
  </div>
  <div class="dots"><i class="on"></i><i></i><i></i><i></i></div>
</section>

<section class="quote-form">
  <h2 class="section-title">Get a Quote</h2>
  <div class="fields">
    <div class="row"><div class="field">Enter Name</div><div class="field">Enter Email</div><div class="field">Enter Phone</div></div>
    <div class="field msg">Leave Message</div>
  </div>
  <div class="submit">Submit</div>
</section>

<footer class="site-footer">
  <div class="copy">Copyright © 2015, Veltra. All Rights Reserved.</div>
  <div class="social"><i></i><i></i><i></i><i></i><i></i></div>
</footer>
</body>
</html>
```